Brell Stone Company Business Cards

Front and Back Business Card - logo and text setup - cool design. I need workable photoshop or illustrator files so I can setup each employee card with design that is created
Updates

Hi everyone, thank you for the great entries. Please no more white and blue cards - there are so many already - black and silver only now please. thanks!

Target Market(s)

Construction Industry - Facility Managers

Industry/Entity Type

Construction

Contact Information for Business Card

I really like contemporary simplistic looks - clean neat....not opposed to seeing some black backrounds

Requirements
Must have
• Logo/website address with design on front only - www.brellstone-example.com (logo attached)
• Back:
• Name/Title/Company Address/Phone/email address
Nice to have
• Cool design
Should not have
• Nothing gimmicky like Fire or Water - since we are a Fire Protection company - it has all been done

```html
<!DOCTYPE html>
<html lang="en">
<head>
<meta charset="utf-8">
<title>Brell Stone Company Business Cards</title>
<link href="https://fonts.googleapis.com/css2?family=Lato:wght@400;700;900&display=swap" rel="stylesheet">
<style>
  :root {
    --backdrop: #4a4a4c;
    --card-dark: #333335;
    --card-dark-mark: #4a4a4d;
    --card-light: #ffffff;
    --navy: #27427a;
    --flame: #ee4a33;
    --white: #ffffff;
  }
  * { margin: 0; padding: 0; box-sizing: border-box; }
  html, body { width: 1200px; height: 1126px; overflow: hidden; }
  body {
    background: var(--backdrop);
    font-family: "Lato", sans-serif;
    position: relative;
  }
  .card {
    position: absolute;
    left: 160px;
    width: 880px;
    height: 503px;
    overflow: hidden;
    box-shadow: 0 6px 18px rgba(0,0,0,0.35);
  }
  .card--front { top: 40px; background: var(--card-dark); }
  .card--back { top: 583px; background: var(--card-light); }

  .front-wordmark {
    position: absolute;
    top: 150px; left: 0; width: 100%;
    text-align: center;
    font-weight: 900;
    font-size: 96px;
    letter-spacing: -1px;
    color: var(--card-dark-mark);
  }
  .front-web {
    position: absolute;
    top: 340px; left: 90px; right: 90px;
    display: flex; align-items: center; gap: 22px;
  }
  .front-web .rule { flex: 1; height: 1px; background: var(--white); }
  .front-web .url {
    color: var(--white);
    font-size: 20px;
    letter-spacing: 3px;
  }
  .front-web .url strong { font-weight: 700; }

  .back-wordmark {
    position: absolute;
    top: 70px; left: 0; width: 100%;
    text-align: center;
    font-weight: 900;
    font-size: 84px;
    letter-spacing: -1px;
    color: var(--navy);
  }
  .back-bands { position: absolute; left: 0; top: 0; width: 880px; height: 503px; }
  .person {
    position: absolute;
    top: 290px; left: 0; width: 440px;
    text-align: right; padding-right: 70px;
    color: var(--white);
  }
  .person .name { font-size: 32px; font-weight: 700; }
  .person .title { font-size: 23px; font-weight: 400; }
  .contact {
    position: absolute;
    top: 312px; left: 520px;
    color: var(--white);
    font-size: 21px; line-height: 1.3;
  }
  .contact .line { display: flex; align-items: center; gap: 10px; }
  .contact .addr { padding-left: 26px; }
  .contact svg { width: 16px; height: 16px; flex: none; }
</style>
</head>
<body>
  <section class="card card--front">
    <div class="front-wordmark">Brell Stone</div>
    <div class="front-web">
      <span class="rule"></span>
      <span class="url">www.<strong>brellstone-example</strong>.com</span>
      <span class="rule"></span>
    </div>
  </section>

  <section class="card card--back">
    <div class="back-wordmark">Brell Stone</div>
    <svg class="back-bands" viewBox="0 0 880 503" aria-hidden="true">
      <polygon fill="var(--navy)" points="0,255 470,255 470,300 482,315 470,330 458,440 0,440"/>
      <polygon fill="var(--flame)" points="470,275 880,275 880,475 456,475 470,330 482,315 470,300"/>
    </svg>
    <div class="person">
      <div class="name">Daniel Mercer</div>
      <div class="title">Managing Director</div>
    </div>
    <div class="contact">
      <div class="addr">Co. Street, Suite, Building</div>
      <div class="addr">City/State, Zip Code</div>
      <div class="line">
        <svg viewBox="0 0 16 16"><path fill="none" stroke="#fff" stroke-width="1.6" d="M3 2 L6 2 L7 5 L5 6.5 Q6.5 9.5 9.5 11 L11 9 L14 10 L14 13 Q8 14 4 9 Q2 6 3 2 Z"/></svg>
        <span>300.555.0142</span>
      </div>
      <div class="line">
        <svg viewBox="0 0 16 16"><rect x="1.5" y="3.5" width="13" height="9" fill="none" stroke="#fff" stroke-width="1.4"/><path d="M1.5 3.5 L8 9 L14.5 3.5" fill="none" stroke="#fff" stroke-width="1.4"/></svg>
        <span>info@brellstone-example.com</span>
      </div>
    </div>
  </section>
</body>
</html>
```